Commercial Swimming Pool - Design-Build Contractor Website Design

I need a new website that will feature our newly developed logo and trade name as well as provide a fully updated site experience. We are not a residential builder - we strictly design and install high-end commercial pools. I need the website to highlight our portfolio and communicate the various types of projects in which we specialize. I want the effect of the site to reflect the high-end nature of our services - projects like the 57th floor spa at the Phila Silver Willow, the aquatic therapy portion of the Phila Ravenhawks training facility, a 5om indoor competition pool for the prestigious Dallowmere Academy, the indoor water park at The Quenwick Lodge or the recent country club renovation projects we've completed in our region (to name a few examples).
Need extra days to review

```html
<!DOCTYPE html>
<html lang="en">
<head>
<meta charset="utf-8">
<title>Corwin Aquatics — Commercial Pools</title>
<link href="https://fonts.googleapis.com/css2?family=Jost:wght@400;500;600&family=Poppins:wght@800&display=swap" rel="stylesheet">
<style>
:root{
  --navy:#1b2453;
  --navy-deep:#141c44;
  --blue:#42b3e4;
  --sky:#3aa6dc;
  --light:#f4f3f2;
  --white:#ffffff;
  --text:#3a3f55;
}
*{margin:0;padding:0;box-sizing:border-box}
html,body{width:1200px;height:4164px;overflow:hidden;background:var(--white)}
body{position:relative;font-family:"Jost",sans-serif;color:var(--text)}
.abs{position:absolute}
.heading{font-family:"Poppins",sans-serif;font-weight:800;color:var(--navy);text-transform:uppercase;letter-spacing:-0.5px;line-height:1.2}
.accent{color:var(--blue)}
.btn{position:absolute;background:var(--blue);color:var(--white);font-size:14px;letter-spacing:1px;text-transform:uppercase;display:flex;align-items:center;justify-content:center}
.rule{position:absolute;height:3px;background:var(--blue)}
.photo{position:absolute}

/* header */
.site-header{position:absolute;left:0;top:0;width:1200px;height:79px;background:var(--white)}
.brand{position:absolute;display:flex;align-items:center;gap:8px;font-weight:600;color:var(--sky);text-transform:uppercase;letter-spacing:1px}
.brand-mark{width:14px;height:14px;background:var(--sky)}
.nav a{position:absolute;font-size:12px;color:var(--navy);text-decoration:none;text-transform:uppercase;letter-spacing:.3px}
.nav a.active::after{content:"";position:absolute;left:0;right:0;bottom:-8px;height:2px;background:var(--navy)}
.call{position:absolute;display:flex;align-items:center}
.call .divider{width:1px;height:32px;background:var(--sky);margin:0 12px 0 10px}
.call small{display:block;font-size:10px;letter-spacing:.8px;text-transform:uppercase}
.call strong{display:block;font-size:15px;font-weight:500}

/* hero */
.hero{position:absolute;left:0;top:79px;width:1200px;height:618px;background:linear-gradient(180deg,#2e7fd8 0%,#7cbfe9 30%,#e8e2d4 45%,#5cc3ea 55%,#2a9fd8 100%)}
.hero-title{position:absolute;left:131px;top:322px;font-size:39px;color:var(--navy)}
.hero-text{position:absolute;left:131px;top:426px;width:450px;font-size:17px;line-height:25px;color:var(--navy)}
.dots{position:absolute;left:563px;top:522px;display:flex;gap:6px}
.dots i{width:7px;height:7px;border-radius:50%;background:var(--navy)}
.dots i.on{background:var(--blue)}

/* welcome */
.welcome-text{position:absolute;left:629px;top:881px;width:440px;font-size:14px;line-height:21.7px;color:#3b3f4d}

/* projects */
.projects{position:absolute;left:0;top:1164px;width:1200px;height:974px;background:var(--light)}
.section-title{position:absolute;left:0;width:1200px;text-align:center;font-size:29px}
.card{position:absolute;width:457px;background:var(--navy)}
.card .photo{position:static;width:100%}
.card p{color:var(--white);font-size:13.5px;line-height:17px;padding:0 22px;display:flex;align-items:center}

/* quality */
.quality{position:absolute;left:0;top:2138px;width:1200px;height:551px;background:linear-gradient(180deg,#8fb6d8 0%,#cfdde8 40%,#e7dccb 60%,#5ec9d9 80%,#3eb7c9 100%)}
.bubble{position:absolute;left:126px;top:53px;width:420px;height:420px;border-radius:50%;background:rgba(255,255,255,.85);text-align:center}
.bubble .heading{font-size:28px;margin-top:95px}
.bubble p{font-size:14px;line-height:21.5px;color:#3b3f4d;width:290px;margin:14px auto 0}

/* what we do */
.services{position:absolute;left:0;top:3533px;width:1200px;height:413px;background:linear-gradient(90deg,#152356 0%,#1e3a78 55%,#244f86 80%,#1a3366 100%)}
.service-item{position:absolute;width:297px;height:34px;border:1px solid rgba(255,255,255,.85);color:var(--white);font-size:13px;padding-left:14px;display:flex;align-items:center;background:rgba(20,28,68,.35)}

/* footer */
.site-footer{position:absolute;left:0;top:3946px;width:1200px;height:218px;background:var(--navy)}
.site-footer .nav a{color:var(--white)}
.copyright{position:absolute;left:0;top:186px;width:1200px;text-align:center;font-size:11px;color:var(--white)}
</style>
</head>
<body>

<header class="site-header">
  <div class="brand" style="left:133px;top:22px;font-size:19px;line-height:1">
    <span class="brand-mark"></span>Corwin Aquatics
  </div>
  <nav class="nav">
    <a href="#" class="active" style="left:357px;top:30px">Home</a>
    <a href="#" style="left:427px;top:30px">About Us</a>
    <a href="#" style="left:516px;top:30px">Services</a>
    <a href="#" style="left:605px;top:30px">Projects</a>
    <a href="#" style="left:695px;top:30px">Portfolio</a>
    <a href="#" style="left:794px;top:30px">Contact Us</a>
  </nav>
  <div class="call" style="left:904px;top:22px;color:var(--navy)">
    <svg width="20" height="20" viewBox="0 0 24 24"><path fill="#3aa6dc" d="M6.6 10.8a15.1 15.1 0 0 0 6.6 6.6l2.2-2.2c.3-.3.7-.4 1-.2 1.1.4 2.3.6 3.6.6.6 0 1 .4 1 1V20c0 .6-.4 1-1 1A17 17 0 0 1 3 4c0-.6.4-1 1-1h3.5c.6 0 1 .4 1 1 0 1.3.2 2.5.6 3.6.1.3 0 .7-.2 1z"/></svg>
    <span class="divider"></span>
    <div><small>Call us</small><strong>+1 555 010 2040</strong></div>
  </div>
</header>

<section class="hero" role="img" aria-label="Resort pool with blue tiles, white parasols and sun loungers under a clear sky">
  <h1 class="heading hero-title">High-End<br>Commercial Pools</h1>
  <p class="hero-text">Lorem Ipsum is simply dummy text of the printing and typesetting industry. Lorem Ipsum has</p>
  <a class="btn" style="left:131px;top:498px;width:142px;height:40px;font-size:17px">Read More</a>
  <div class="dots"><i></i><i></i><i class="on"></i><i></i><i></i></div>
</section>

<section class="welcome">
  <div class="photo" role="img" aria-label="Rippling blue pool water" style="left:261px;top:748px;width:364px;height:364px;border-radius:50%;background:radial-gradient(circle at 60% 50%,#8fd8f5,#1f8fd6 70%,#0f6bb8)"></div>
  <div class="photo" role="img" aria-label="Hillside resort pool at sunset" style="left:133px;top:749px;width:362px;height:362px;border-radius:50%;background:linear-gradient(180deg,#3a4a6a 0%,#c88a4c 35%,#6f5a44 60%,#2e6d8c 100%)"></div>
  <h2 class="heading abs" style="left:629px;top:758px;font-size:29px">Welcome to<br><span class="accent">Corwin Aquatics</span></h2>
  <div class="rule" style="left:629px;top:843px;width:121px"></div>
  <p class="welcome-text">Sed ut perspiciatis unde omnis iste natus error sit voluptatem accusantium doloremque laudantium, totam rem aperiam, eaque ipsa quae ab illo inventore veritatis et quasi architecto beatae vitae dicta sunt explicabo. Nemo enim ipsam voluptatem quia voluptas sit aspernatur aut odit aut fugit, sed quia consequuntur magni dolores eos qui ratione voluptatem sequi nesciunt. Neque porro quisquam est, qui dolorem ipsum quia.</p>
  <a class="btn" style="left:629px;top:1069px;width:117px;height:33px">Read More</a>
</section>

<section class="projects">
  <h2 class="heading section-title" style="top:40px">Our <span class="accent">Projects</span></h2>
  <div class="rule" style="left:558px;top:90px;width:42px"></div>

  <article class="card" style="left:133px;top:125px">
    <div class="photo" role="img" aria-label="Illuminated resort pool with ladder at dusk" style="height:305px;background:linear-gradient(180deg,#2b3f73 0%,#c27a3c 45%,#5a3fa8 75%,#6a4f7a 100%)"></div>
    <p style="height:55px">57th floor spa at the Phila Silver Willow</p>
  </article>
  <article class="card" style="left:608px;top:125px">
    <div class="photo" role="img" aria-label="Rooftop lap pool overlooking a city" style="height:305px;background:linear-gradient(180deg,#aeb3b8 0%,#d4d6d6 40%,#6e8a8e 60%,#3fb5c9 100%)"></div>
    <p style="height:55px">The aquatic therapy portion of the Phila Ravenhawks training facility</p>
  </article>
  <article class="card" style="left:133px;top:506px">
    <div class="photo" role="img" aria-label="Lagoon pool with palm trees and stone edging" style="height:306px;background:linear-gradient(180deg,#d9dcdc 0%,#7f9a66 40%,#4c7a44 65%,#2fa6d6 100%)"></div>
    <p style="height:61px">a 5om indoor competition pool for the prestigious<br>Dallowmere Academy</p>
  </article>
  <article class="card" style="left:608px;top:506px">
    <div class="photo" role="img" aria-label="Curved pool with cabana loungers and umbrellas" style="height:306px;background:linear-gradient(180deg,#5f8a4a 0%,#9aa57a 35%,#2bb6cf 65%,#d9cfc0 100%)"></div>
    <p style="height:61px">The indoor water park at The Quenwick Lodge or the<br>recent country club renovation projects</p>
  </article>

  <a class="btn" style="left:511px;top:901px;width:178px;height:32px">View All Projects</a>
</section>

<section class="quality" role="img" aria-label="Beachfront resort pool lined with palm trees and loungers">
  <div class="bubble">
    <h2 class="heading">High Quality<br><span class="accent">Materials &amp;<br>Equipment</span></h2>
    <p>Sed ut perspiciatis unde omnis iste natus error sit voluptatem accusantium dolor emque laudantium, totam rem aperiam, eaque ipsa quae ab illo inventore veritatis et quasi architecto beatae vitae</p>
  </div>
  <a class="btn" style="left:276px;top:383px;width:119px;height:32px">Read More</a>
</section>

<section class="portfolio">
  <h2 class="heading section-title" style="top:2726px">Our <span class="accent">Portfolio</span></h2>
  <div class="rule" style="left:579px;top:2777px;width:42px"></div>
  <div class="photo" role="img" aria-label="Pool beside a tiled pavilion and trees" style="left:44px;top:2825px;width:360px;height:291px;background:linear-gradient(180deg,#4f7a3c,#7ea25a 45%,#2fd0e0 75%,#29c1da)"></div>
  <div class="photo" role="img" aria-label="Hotel pool with stone deck and terrace" style="left:422px;top:2825px;width:359px;height:291px;background:linear-gradient(180deg,#6f6a45,#c9b88d 40%,#33c1dc 70%,#20a9cf)"></div>
  <div class="photo" role="img" aria-label="Infinity pool above a city skyline at dusk" style="left:799px;top:2825px;width:359px;height:291px;background:linear-gradient(180deg,#b9d0d8,#e9d98a 40%,#4c6f7a 70%,#24556a)"></div>
  <div class="photo" role="img" aria-label="Blue tiled pool steps" style="left:44px;top:3137px;width:360px;height:291px;background:linear-gradient(135deg,#4a84c8,#2e63b0 50%,#5fa0de)"></div>
  <div class="photo" role="img" aria-label="Resort pool lit at night with palms" style="left:422px;top:3137px;width:359px;height:291px;background:linear-gradient(180deg,#0c1420,#1f3a3a 45%,#2aa7cf 75%,#103a5a)"></div>
  <div class="photo" role="img" aria-label="Rooftop pool with towers at sunset" style="left:799px;top:3137px;width:359px;height:291px;background:linear-gradient(180deg,#6f7fa4,#d9a48e 40%,#5a6f8f 65%,#2b3f66)"></div>
  <a class="btn" style="left:551px;top:3457px;width:101px;height:32px">View All</a>
</section>

<section class="services" role="img" aria-label="Night city skyline behind an illuminated rooftop pool">
  <h2 class="heading section-title" style="top:40px;color:var(--white)">More of&nbsp; <span class="accent">What We Do</span></h2>
  <div class="rule" style="left:579px;top:94px;width:42px"></div>
  <div class="service-item" style="left:296px;top:138px">Lorem Ipsum is simply dummy text of the</div>
  <div class="service-item" style="left:296px;top:186px">It is a long established fact that a reade</div>
  <div class="service-item" style="left:296px;top:233px">Contrary to popular belief, Lorem Ipsu</div>
  <div class="service-item" style="left:296px;top:282px">Neque porro quisquam est, qui dolorem</div>
  <div class="service-item" style="left:296px;top:330px">But I must explain to you how all</div>
  <div class="service-item" style="left:613px;top:138px">Lorem Ipsum is simply dummy text of the</div>
  <div class="service-item" style="left:613px;top:186px">It is a long established fact that a reade</div>
  <div class="service-item" style="left:613px;top:233px">Contrary to popular belief, Lorem Ipsu</div>
  <div class="service-item" style="left:613px;top:282px">Neque porro quisquam est, qui dolorem</div>
  <div class="service-item" style="left:613px;top:330px">But I must explain to you how all</div>
</section>

<footer class="site-footer">
  <div class="brand" style="left:133px;top:52px;font-size:28px;line-height:1;color:var(--white)">
    <span class="brand-mark" style="width:20px;height:20px;background:var(--white)"></span>Corwin Aquatics
  </div>
  <div class="abs" style="left:712px;top:55px;font-size:11px;color:var(--white);letter-spacing:.8px">FOLLOW US</div>
  <div class="call" style="left:904px;top:42px;color:var(--white)">
    <svg width="20" height="20" viewBox="0 0 24 24"><path fill="#3aa6dc" d="M6.6 10.8a15.1 15.1 0 0 0 6.6 6.6l2.2-2.2c.3-.3.7-.4 1-.2 1.1.4 2.3.6 3.6.6.6 0 1 .4 1 1V20c0 .6-.4 1-1 1A17 17 0 0 1 3 4c0-.6.4-1 1-1h3.5c.6 0 1 .4 1 1 0 1.3.2 2.5.6 3.6.1.3 0 .7-.2 1z"/></svg>
    <span class="divider"></span>
    <div><small>Call us</small><strong>+1 555 010 2040</strong></div>
  </div>
  <nav class="nav">
    <a href="#" style="left:556px;top:97px">Home</a>
    <a href="#" style="left:624px;top:97px">About Us</a>
    <a href="#" style="left:713px;top:97px">Services</a>
    <a href="#" style="left:800px;top:97px">Projects</a>
    <a href="#" style="left:891px;top:97px">Portfolio</a>
    <a href="#" style="left:988px;top:97px">Contact Us</a>
  </nav>
  <div class="abs" style="left:133px;top:142px;width:933px;height:1px;background:rgba(255,255,255,.25)"></div>
  <p class="copyright">Copyright © 2023 All Rights Reserved</p>
</footer>

</body>
</html>
```